New Website for Manufacturing Company - PSD only, no coding - CLOSED TO NEW DESIGNERS

IF YOU HAVE NOT ALREADY SUBMITTED A DESIGN PLEASE DO NOT SUBMIT ONE.
This is a re-work of an existing website. We can keep the themes and color schemes the same but we will be changing the layout and page content.
The scope includes the creation of some icons/sketches that will form some of the page content.
The scope is design only, no coding.
There are four files that have been uploaded that give a more detailed project brief, please read them.
Target Market(s)
Manufacturing
Industry/Entity Type
It Company
Number of Pages Required
1 page

```html
<!DOCTYPE html>
<html lang="en">
<head>
<meta charset="utf-8">
<title>Kestrel – High Temperature Insulation</title>
<link href="https://fonts.googleapis.com/css2?family=Open+Sans:wght@400;600;700;800&display=swap" rel="stylesheet">
<style>
:root{
  --navy:#12335f;
  --blue:#1c5aa6;
  --blue-dark:#0e2c55;
  --sky:#e9eef4;
  --grey:#f4f5f7;
  --line:#d9dde3;
  --text:#4a4f57;
  --muted:#8a9099;
  --white:#ffffff;
}
*{box-sizing:border-box;margin:0;padding:0}
html,body{width:880px;height:1200px;overflow:hidden}
body{font-family:"Open Sans",Arial,sans-serif;color:var(--text);background:var(--white);position:relative}
.site-header{height:76px;display:flex;align-items:center;padding:0 40px;position:relative}
.brand{display:flex;align-items:center;gap:8px;font-weight:800;font-size:28px;color:var(--blue);letter-spacing:1px}
.brand-square{width:14px;height:14px;background:var(--blue)}
.tagline{margin-left:18px;font-size:12px;font-weight:600;color:var(--navy);letter-spacing:.5px}
.header-contact{position:absolute;right:40px;top:22px;font-size:10px;color:var(--muted);line-height:17px}
.header-contact div{display:flex;align-items:center;gap:6px}
.main-nav{height:26px;background:var(--blue);display:flex;align-items:center;padding:0 40px 0 40px}
.main-nav a{color:var(--white);font-size:9px;font-weight:600;text-decoration:none;padding:0 13px;height:26px;line-height:26px;text-transform:uppercase}
.main-nav a.active{background:var(--blue-dark)}
.search{margin-left:auto;width:150px;height:16px;background:var(--white);display:flex;justify-content:flex-end;align-items:center;padding-right:4px}
.hero{height:196px;background:var(--grey);position:relative;display:flex;align-items:center}
.hero-visual{position:absolute;left:80px;top:14px;width:300px;height:168px;background:linear-gradient(180deg,#f7f8fa,#dfe4ea);border-radius:4px}
.hero-copy{position:absolute;left:440px;top:48px;line-height:1.05}
.hero-copy .big{font-size:30px;font-weight:800;color:var(--blue);letter-spacing:1px}
.hero-copy .mid{font-size:20px;font-weight:600;color:var(--navy);letter-spacing:1px}
.hero-copy .mid b{color:var(--blue);font-weight:800;font-size:26px}
.arrow{position:absolute;top:82px}
.capabilities{padding-top:34px;text-align:center}
.section-title{font-size:17px;font-weight:600;color:var(--text)}
.rule{width:60px;height:1px;background:var(--line);margin:8px auto 0}
.cap-grid{display:grid;grid-template-columns:repeat(4,176px);gap:30px 20px;justify-content:center;margin-top:16px}
.cap-card{border:1px solid var(--line);background:var(--white);height:206px;display:flex;flex-direction:column}
.cap-img{height:92px;margin:10px 30px 0;background:linear-gradient(180deg,#f3f4f6,#d8dce2);border-radius:3px}
.cap-card h3{font-size:11px;font-weight:600;margin-top:12px;color:var(--text)}
.cap-card p{font-size:8px;color:var(--muted);line-height:12px;padding:4px 18px 0;height:34px}
.read-more{margin-top:auto;height:22px;background:var(--blue);color:var(--white);font-size:8px;line-height:22px;font-weight:600}
.about{text-align:center;padding-top:34px}
.about p{width:600px;margin:14px auto 0;font-size:9px;line-height:14px;color:var(--muted)}
.site-footer{position:absolute;left:0;top:1016px;width:880px;height:184px;background:var(--navy);color:var(--white)}
.footer-cols{display:flex;gap:0;padding:22px 40px 0}
.footer-col{width:133px}
.footer-col h4{font-size:9px;font-weight:700;letter-spacing:.5px;margin-bottom:8px}
.footer-col li{list-style:none;font-size:8px;line-height:13px;color:#b9c7da}
.footer-bottom{position:absolute;left:0;bottom:0;width:100%;height:26px;border-top:1px solid #274a78;display:flex;align-items:center;padding:0 40px;font-size:8px;color:#b9c7da}
.footer-bottom span:last-child{margin-left:auto}
</style>
</head>
<body>
<header class="site-header">
  <div class="brand"><span class="brand-square"></span>KESTREL</div>
  <div class="tagline">"HIGH TEMPERATURE INSULATION EXPERTS"</div>
  <div class="header-contact">
    <div><svg width="9" height="9" viewBox="0 0 10 10"><path d="M2 1l2 2-1 1.5a6 6 0 0 0 2.5 2.5L7 6l2 2-1.5 1.5C4 9 1 6 .5 2.5z" fill="#8a9099"/></svg>Call Us: 1-800-555-0142</div>
    <div><svg width="9" height="9" viewBox="0 0 10 10"><rect x=".5" y="2" width="9" height="6" fill="none" stroke="#8a9099"/><path d="M.5 2l4.5 3.5L9.5 2" fill="none" stroke="#8a9099"/></svg>E-mail: info@kestrelmfg.com</div>
  </div>
</header>
<nav class="main-nav">
  <a class="active">Home</a><a>Find</a><a>Industrial</a><a>Custom Manufacturing</a><a>About Us</a><a>Contact Us</a>
  <div class="search"><svg width="9" height="9" viewBox="0 0 10 10"><circle cx="4" cy="4" r="3" fill="none" stroke="#1c5aa6" stroke-width="1.4"/><path d="M6.3 6.3l3 3" stroke="#1c5aa6" stroke-width="1.4"/></svg></div>
</nav>
<section class="hero">
  <svg class="arrow" style="left:14px" width="12" height="24" viewBox="0 0 12 24"><path d="M10 2L2 12l8 10" fill="none" stroke="#8a9099" stroke-width="2"/></svg>
  <div class="hero-visual" role="img" aria-label="Line sketch of an insulated industrial appliance component"></div>
  <div class="hero-copy">
    <div class="big">MANUFACTURER</div>
    <div class="mid">FABRICATOR AND DISTRIBUTOR</div>
    <div class="mid">OF HIGH TEMPERATURE</div>
    <div class="mid"><b>INSULATING</b> MATERIALS</div>
  </div>
  <svg class="arrow" style="right:14px" width="12" height="24" viewBox="0 0 12 24"><path d="M2 2l8 10-8 10" fill="none" stroke="#8a9099" stroke-width="2"/></svg>
</section>
<section class="capabilities">
  <h2 class="section-title">Our Capabilities</h2>
  <div class="rule"></div>
  <div class="cap-grid">
    <div class="cap-card"><div class="cap-img" role="img" aria-label="Sketch of material cutting"></div><h3>Material Cutting</h3><p>Precise cuts in many high heat materials.</p><div class="read-more">Read More</div></div>
    <div class="cap-card"><div class="cap-img" role="img" aria-label="Sketch of coating process"></div><h3>Coating</h3><p>Even protective coats for demanding parts.</p><div class="read-more">Read More</div></div>
    <div class="cap-card"><div class="cap-img" role="img" aria-label="Sketch of CNC machined block"></div><h3>CNC Machining</h3><p>Tight tolerance shapes from rigid boards.</p><div class="read-more">Read More</div></div>
    <div class="cap-card"><div class="cap-img" role="img" aria-label="Sketch of laminated sheets"></div><h3>Laminating</h3><p>Layered sheets bonded for added strength.</p><div class="read-more">Read More</div></div>
    <div class="cap-card"><div class="cap-img" role="img" aria-label="Sketch of slitting roll"></div><h3>Slitting</h3><p>Rolls slit to exact widths on demand.</p><div class="read-more">Read More</div></div>
    <div class="cap-card"><div class="cap-img" role="img" aria-label="Sketch of die cut gasket"></div><h3>Die Cutting</h3><p>Clean repeatable gaskets in large runs.</p><div class="read-more">Read More</div></div>
    <div class="cap-card"><div class="cap-img" role="img" aria-label="Sketch of vacuum formed part"></div><h3>Vacuum Forming</h3><p>Custom formed shapes for complex spaces.</p><div class="read-more">Read More</div></div>
    <div class="cap-card"><div class="cap-img" role="img" aria-label="Sketch of assorted insulation products"></div><h3>Other Capabilities</h3><p>Kitting, assembly and special fabrication.</p><div class="read-more">Read More</div></div>
  </div>
</section>
<section class="about">
  <h2 class="section-title">About Us</h2>
  <div class="rule"></div>
  <p>We are the largest and most reliable supplier of refractory and insulation products in the region, an independent manufacturer and distributor of a wide variety of high temperature materials serving many industrial markets since our founding.</p>
</section>
<footer class="site-footer">
  <div class="footer-cols">
    <div class="footer-col"><h4>CAPABILITIES</h4><ul><li>cutting</li><li>vacuum forming</li><li>slitting</li><li>laminate cutting</li><li>cnc machining</li><li>die cutting</li></ul></div>
    <div class="footer-col"><h4>SERVICES</h4><ul><li>design</li><li>rapid prototyping</li><li>kitting</li><li>assembly</li></ul></div>
    <div class="footer-col"><h4>MARKETS</h4><ul><li>appliance</li><li>food</li><li>automotive</li><li>petrochemical</li></ul></div>
    <div class="footer-col"><h4>MATERIALS</h4><ul><li>ceramic paper</li><li>fiberglass</li><li>gaskets</li><li>mineral wool</li><li>rope</li></ul></div>
    <div class="footer-col"><h4>DOCUMENTATION</h4><ul><li>spec sheets</li><li>safety data</li><li>terms of sale</li></ul></div>
    <div class="footer-col"><h4>CONTACT US</h4><ul><li>1-800-555-0142</li><li>info@kestrelmfg.com</li></ul></div>
  </div>
  <div class="footer-bottom"><span>© 2015 Kestrel Manufacturing. All Rights Reserved.</span><span>▲</span></div>
</footer>
</body>
</html>
```